Website Design for a holiday home letting busines

We require a redesign of our present website www.pinebrookstays.com. We want the website to stand out and look professional and clean to make holiday hunters want to book a caravan or lodge holiday with us. Our logo is red however we DO NOT want the website to be red. We want a natural colour scheme.

The final design should communicate that we are a professional company to book with.

On the home page we require;
Overview of company
Photo
Search box for holiday (check in)
Late Deals
Reviews
News

We would like the following pages designed; home page, available dates page, caravans page, content page.

The website should be responsive for smart phones. One website I do like is http://www.verdoliso.be/nl/

Target Market(s)

Families

Industry/Entity Type

Travel

Number of Pages Required

5+ page

Font styles to use
Serif

Requirements
Must have
• The project must be responsive for mobile phones and tablets.
• Ability to search for holiday home holidays
• We want a natural colour scheme.
Nice to have
• A style we like is http://www.verdoliso.be/nl/
Should not have
• Do not use red as a colour for the website. Our logo is red so this is the only time we want this used.

```html
<!DOCTYPE html>
<html lang="en">
<head>
<meta charset="utf-8">
<title>Pinebrook Stays – Holiday Lodges &amp; Caravans</title>
<link href="https://fonts.googleapis.com/css2?family=Oswald:wght@500;700&family=Roboto+Slab:wght@400;700&family=Open+Sans:wght@400;600;700&display=swap" rel="stylesheet">
<style>
:root{
  --navy:#1c2b3a;
  --navy-deep:#17222d;
  --blue:#2b7fc3;
  --blue-dark:#1f6aa8;
  --text:#4a4f55;
  --muted:#8a9096;
  --line:#e2e5e8;
  --bg:#ffffff;
  --panel:#f4f6f8;
  --footer:#1e2831;
  --footer-bottom:#161e25;
  --brand:#c8312d;
}
*{box-sizing:border-box;margin:0;padding:0}
html,body{width:1200px;height:2884px;overflow:hidden}
body{background:var(--bg);font-family:"Open Sans",sans-serif;color:var(--text);font-size:13px;position:relative}
.wrap{width:1000px;margin:0 auto;position:relative}
.heading{font-family:"Roboto Slab",serif;color:var(--blue);font-weight:700;font-size:22px;letter-spacing:1px;text-transform:uppercase}

/* header */
.site-header{height:130px;display:flex;align-items:center}
.site-header .wrap{display:flex;justify-content:space-between;align-items:center}
.brand{display:flex;align-items:center;gap:12px}
.brand-dot{width:34px;height:34px;border-radius:50%;background:var(--brand)}
.brand-name{font-family:"Open Sans",sans-serif;font-weight:700;font-size:26px;color:var(--navy)}
.brand-sub{font-size:12px;color:var(--muted);margin-top:2px}
.contact-line{display:flex;gap:26px;font-size:13px;color:var(--navy);font-weight:600}
.contact-line span{display:flex;align-items:center;gap:7px}

/* nav */
.main-nav{height:48px;background:var(--navy);position:relative}
.main-nav ul{list-style:none;display:flex;height:48px;width:1000px;margin:0 auto;justify-content:space-between}
.main-nav li{color:#cfd6dd;font-size:11px;font-weight:700;letter-spacing:.5px;display:flex;align-items:center;padding:0 12px}
.main-nav li.active{background:var(--blue);color:#fff}
.live-chat{position:absolute;right:0;top:54px;background:var(--blue);color:#fff;font-size:11px;font-weight:700;padding:9px 14px;border-radius:4px 0 0 4px;z-index:3}

/* hero */
.hero{height:422px;position:relative;background:linear-gradient(180deg,#5b5346 0%,#8b7c66 45%,#a9977c 70%,#6e6251 100%)}
.hero-copy{position:absolute;left:100px;top:90px;color:#fff}
.hero-copy h1{font-family:"Oswald",sans-serif;font-size:64px;font-weight:700;letter-spacing:1px;line-height:1}
.hero-copy p{font-size:15px;margin-top:18px;width:480px;line-height:1.5;font-weight:600}
.hero-arrow{position:absolute;top:190px;width:34px;height:44px;background:rgba(0,0,0,.3);display:flex;align-items:center;justify-content:center}
.hero-arrow.left{left:0}.hero-arrow.right{right:0}

/* booking */
.booking{height:145px;padding-top:28px;background:#fff}
.booking .heading{text-align:center;font-size:24px}
.booking-bar{margin:18px auto 0;width:1000px;height:56px;background:var(--panel);border:1px solid var(--line);display:flex;align-items:center;gap:14px;padding:0 14px}
.field{height:34px;background:#fff;border:1px solid var(--line);flex:1;display:flex;align-items:center;justify-content:space-between;padding:0 12px;color:var(--muted);font-size:11px;font-weight:600}
.btn{background:var(--blue);color:#fff;font-weight:700;font-size:11px;letter-spacing:.5px;text-transform:uppercase;display:flex;align-items:center;justify-content:center}
.booking-bar .btn{height:34px;width:220px}

/* overview */
.overview{height:295px;padding-top:18px}
.overview .wrap{display:flex;gap:40px}
.overview-text{flex:1}
.overview-text p{font-size:12.5px;line-height:1.75;margin-top:14px}
.overview-text a{color:var(--blue);font-weight:600}
.video{width:370px;height:210px;margin-top:28px;background:linear-gradient(160deg,#6fa8d8 0%,#9cc3a0 55%,#5c8a4f 100%);position:relative}
.video-title{position:absolute;top:0;left:0;right:0;background:rgba(0,0,0,.55);color:#fff;font-size:11px;padding:6px 10px;font-weight:600}

/* cards */
.deals{height:530px;padding-top:10px}
.listing{height:530px;padding-top:10px}
.section-top{display:flex;justify-content:space-between;align-items:center}
.pager{display:flex;gap:6px}
.pager span{width:22px;height:22px;border:1px solid var(--line);display:flex;align-items:center;justify-content:center}
.cards{display:flex;gap:50px;margin-top:22px}
.card{width:300px;border:1px solid var(--line);background:#fff}
.card-photo{height:178px}
.card-body{padding:16px 16px 18px}
.card-title{font-size:14px;font-weight:700;color:var(--navy)}
.card-date{font-size:14px;color:var(--text);margin-top:3px}
.card-specs{display:flex;justify-content:space-between;margin-top:22px;font-size:10px;font-weight:700;color:var(--muted);letter-spacing:.4px}
.card-icons{display:flex;justify-content:space-between;margin-top:16px;padding-top:14px;border-top:1px solid var(--line)}
.card-icons span{display:flex;align-items:center;gap:8px;font-size:11px;color:var(--muted);width:48%}
.card .btn{height:34px;width:170px;margin:18px auto 0}

/* triple columns */
.feeds{height:510px;padding-top:12px}
.feeds .wrap{display:flex;gap:25px}
.feed{width:316px;border:1px solid var(--line)}
.feed-head{background:var(--blue);color:#fff;font-family:"Roboto Slab",serif;font-weight:700;font-size:16px;letter-spacing:1px;padding:11px 14px;display:flex;align-items:center;gap:9px}
.review{padding:14px 16px 8px}
.review h4{font-family:"Roboto Slab",serif;color:var(--blue);font-size:13px;letter-spacing:.5px}
.review .stayed{font-size:11px;color:var(--blue);font-weight:600;margin-top:3px}
.review p{font-size:11px;line-height:1.6;color:var(--muted);margin-top:6px}
.post{display:flex;gap:12px;padding:12px 14px 10px;border-bottom:1px solid var(--line)}
.post:last-child{border-bottom:0}
.thumb{width:88px;height:80px;flex:none}
.post h4{font-family:"Roboto Slab",serif;color:var(--blue);font-size:12px;letter-spacing:.4px}
.post p{font-size:10.5px;line-height:1.55;color:var(--muted);margin-top:4px}
.post .meta{font-size:10px;color:var(--muted);margin-top:5px}
.post .likes{display:flex;gap:12px;margin-top:5px;font-size:10px;color:var(--blue);font-weight:600}

/* footer */
.site-footer{position:absolute;left:0;top:2610px;width:1200px;height:274px;background:var(--footer);color:#aeb6be}
.footer-cols{display:flex;gap:30px;padding-top:26px}
.footer-col{flex:1}
.footer-col h5{color:#fff;font-size:12px;letter-spacing:1px;font-weight:700;margin-bottom:14px}
.footer-col li{list-style:none;font-size:11px;line-height:2;padding-left:12px;position:relative}
.footer-col li:before{content:"";position:absolute;left:0;top:10px;width:4px;height:4px;background:var(--blue)}
.subscribe{height:30px;background:#fff;width:230px;margin-bottom:10px}
.footer-col .btn{width:120px;height:28px}
.footer-bottom{position:absolute;left:0;bottom:0;width:1200px;height:46px;background:var(--footer-bottom)}
.footer-bottom .wrap{display:flex;justify-content:space-between;align-items:center;height:46px;font-size:11px}
.top-link{width:28px;height:28px;border:1px solid #3a4652;display:flex;align-items:center;justify-content:center;font-size:10px;color:#fff}
</style>
</head>
<body>

<header class="site-header">
  <div class="wrap">
    <div class="brand">
      <div class="brand-dot"></div>
      <div>
        <div class="brand-name">Pinebrook Stays</div>
        <div class="brand-sub">at Fernside Castle Holiday Park</div>
      </div>
    </div>
    <div class="contact-line">
      <span><svg width="14" height="14" viewBox="0 0 24 24"><path fill="#2b7fc3" d="M6.6 10.8a15 15 0 006.6 6.6l2.2-2.2c.3-.3.7-.4 1-.2 1.1.4 2.3.6 3.6.6.6 0 1 .4 1 1V20c0 .6-.4 1-1 1A17 17 0 013 4c0-.6.4-1 1-1h3.5c.6 0 1 .4 1 1 0 1.3.2 2.5.6 3.6.1.3 0 .7-.2 1z"/></svg>01632 960 418</span>
      <span><svg width="14" height="12" viewBox="0 0 24 20"><rect x="1" y="1" width="22" height="18" fill="none" stroke="#2b7fc3" stroke-width="2"/><path d="M1 1l11 9 11-9" fill="none" stroke="#2b7fc3" stroke-width="2"/></svg>info@pinebrookstays.com</span>
    </div>
  </div>
</header>

<nav class="main-nav">
  <ul>
    <li class="active">HOME</li><li>NEWS</li><li>BOOKING</li><li>CARAVANS &amp; LODGES</li><li>2014 HOLIDAYS</li><li>2015 HOLIDAYS</li><li>PAYMENT PLANS</li><li>FERNSIDE CASTLE</li><li>LOCAL ATTRACTIONS</li><li>CONTACT US</li>
  </ul>
  <div class="live-chat">LIVE CHAT</div>
</nav>

<section class="hero" role="img" aria-label="Photo of a bright lodge living room interior">
  <div class="hero-arrow left"><svg width="12" height="20" viewBox="0 0 12 20"><path d="M10 2L2 10l8 8" fill="none" stroke="#fff" stroke-width="2.5"/></svg></div>
  <div class="hero-arrow right"><svg width="12" height="20" viewBox="0 0 12 20"><path d="M2 2l8 8-8 8" fill="none" stroke="#fff" stroke-width="2.5"/></svg></div>
  <div class="hero-copy">
    <h1>NO DEPOSIT HOLIDAYS</h1>
    <p>Would you like to book a 2015 caravan or lodge holiday at Fernside Castle Holiday Park with no deposit?</p>
  </div>
</section>

<section class="booking">
  <div class="heading">Book Here</div>
  <div class="booking-bar">
    <div class="field">CHECK IN DATE <span>▾</span></div>
    <div class="field">NO. OF NIGHTS <span>▾</span></div>
    <div class="field">CARAVAN TYPE <span>▾</span></div>
    <div class="btn">Check Holiday To Book</div>
  </div>
</section>

<section class="overview">
  <div class="wrap">
    <div class="overview-text">
      <div class="heading">Overview of Company</div>
      <p>We have flexible low cost holiday payment plans available so you can spread the cost of your stay over the months before you arrive. This means your break can be booked today without any large upfront payment being taken from you.</p>
      <p>Once you add to the check dates available, payments start within 21 days. You then get the option to choose when any of the weekly or monthly payments are taken from your bank. If you prefer to make a full payment to secure the date, this can be accepted with the balance due 8 weeks before your holiday.</p>
      <p>If you have any questions about our hassle free direct debit payment plans please contact us and we will be more than happy to help ... <a>read more »</a></p>
    </div>
    <div class="video" role="img" aria-label="Video preview of holiday lodges beside a lawn">
      <div class="video-title">Private Lodge and Caravan Hire at Fernside</div>
    </div>
  </div>
</section>

<section class="deals">
  <div class="wrap">
    <div class="section-top">
      <div class="heading">Late Deals</div>
      <div class="pager"><span><svg width="6" height="10" viewBox="0 0 6 10"><path d="M5 1L1 5l4 4" fill="none" stroke="#2b7fc3" stroke-width="1.6"/></svg></span><span><svg width="6" height="10" viewBox="0 0 6 10"><path d="M1 1l4 4-4 4" fill="none" stroke="#2b7fc3" stroke-width="1.6"/></svg></span></div>
    </div>
    <div class="cards">
      <article class="card">
        <div class="card-photo" role="img" aria-label="Photo of a caravan lounge" style="background:linear-gradient(150deg,#c9a878,#7a5a3c)"></div>
        <div class="card-body">
          <div class="card-title">The Marigold</div>
          <div class="card-date">Friday 04 September 2015 (3 nights)</div>
          <div class="card-specs"><span>CARAVAN TYPE</span><span>CARAVAN TYPE</span></div>
          <div class="card-icons"><span><svg width="18" height="12" viewBox="0 0 18 12"><rect x="0" y="5" width="18" height="5" fill="#2b7fc3"/><rect x="0" y="1" width="6" height="4" fill="#2b7fc3"/></svg>3 Beds</span><span><svg width="14" height="14" viewBox="0 0 14 14"><circle cx="7" cy="4" r="3" fill="#2b7fc3"/><rect x="2" y="8" width="10" height="6" rx="2" fill="#2b7fc3"/></svg>8 Guests</span></div>
          <div class="btn">Book Now For £189</div>
        </div>
      </article>
      <article class="card">
        <div class="card-photo" role="img" aria-label="Photo of a lodge bedroom" style="background:linear-gradient(150deg,#d8c3a0,#8c6d4c)"></div>
        <div class="card-body">
          <div class="card-title">The Marigold</div>
          <div class="card-date">Friday 04 September 2015 (3 nights)</div>
          <div class="card-specs"><span>CARAVAN TYPE</span><span>CARAVAN TYPE</span></div>
          <div class="card-icons"><span><svg width="18" height="12" viewBox="0 0 18 12"><rect x="0" y="5" width="18" height="5" fill="#2b7fc3"/><rect x="0" y="1" width="6" height="4" fill="#2b7fc3"/></svg>3 Beds</span><span><svg width="14" height="14" viewBox="0 0 14 14"><circle cx="7" cy="4" r="3" fill="#2b7fc3"/><rect x="2" y="8" width="10" height="6" rx="2" fill="#2b7fc3"/></svg>8 Guests</span></div>
          <div class="btn">Book Now For £189</div>
        </div>
      </article>
      <article class="card">
        <div class="card-photo" role="img" aria-label="Photo of a caravan dining area" style="background:linear-gradient(150deg,#b89a74,#5e4632)"></div>
        <div class="card-body">
          <div class="card-title">The Marigold</div>
          <div class="card-date">Friday 04 September 2015 (3 nights)</div>
          <div class="card-specs"><span>CARAVAN TYPE</span><span>CARAVAN TYPE</span></div>
          <div class="card-icons"><span><svg width="18" height="12" viewBox="0 0 18 12"><rect x="0" y="5" width="18" height="5" fill="#2b7fc3"/><rect x="0" y="1" width="6" height="4" fill="#2b7fc3"/></svg>3 Beds</span><span><svg width="14" height="14" viewBox="0 0 14 14"><circle cx="7" cy="4" r="3" fill="#2b7fc3"/><rect x="2" y="8" width="10" height="6" rx="2" fill="#2b7fc3"/></svg>8 Guests</span></div>
          <div class="btn">Book Now For £189</div>
        </div>
      </article>
    </div>
  </div>
</section>

<section class="listing">
  <div class="wrap">
    <div class="section-top">
      <div class="heading">List of Caravans and Lodges</div>
      <div class="pager"><span><svg width="6" height="10" viewBox="0 0 6 10"><path d="M5 1L1 5l4 4" fill="none" stroke="#2b7fc3" stroke-width="1.6"/></svg></span><span><svg width="6" height="10" viewBox="0 0 6 10"><path d="M1 1l4 4-4 4" fill="none" stroke="#2b7fc3" stroke-width="1.6"/></svg></span></div>
    </div>
    <div class="cards">
      <article class="card">
        <div class="card-photo" role="img" aria-label="Photo of a lodge bedroom" style="background:linear-gradient(150deg,#cdb28c,#6f5439)"></div>
        <div class="card-body">
          <div class="card-title">The Marigold</div>
          <div class="card-date">Friday 04 September 2015 (3 nights)</div>
          <div class="card-specs"><span>CARAVAN TYPE</span><span>CARAVAN TYPE</span></div>
          <div class="card-icons"><span><svg width="18" height="12" viewBox="0 0 18 12"><rect x="0" y="5" width="18" height="5" fill="#2b7fc3"/><rect x="0" y="1" width="6" height="4" fill="#2b7fc3"/></svg>3 Beds</span><span><svg width="14" height="14" viewBox="0 0 14 14"><circle cx="7" cy="4" r="3" fill="#2b7fc3"/><rect x="2" y="8" width="10" height="6" rx="2" fill="#2b7fc3"/></svg>8 Guests</span></div>
          <div class="btn">Book Now For £189</div>
        </div>
      </article>
      <article class="card">
        <div class="card-photo" role="img" aria-label="Photo of a caravan kitchen" style="background:linear-gradient(150deg,#e0cfb2,#9a7b58)"></div>
        <div class="card-body">
          <div class="card-title">The Marigold</div>
          <div class="card-date">Friday 04 September 2015 (3 nights)</div>
          <div class="card-specs"><span>CARAVAN TYPE</span><span>CARAVAN TYPE</span></div>
          <div class="card-icons"><span><svg width="18" height="12" viewBox="0 0 18 12"><rect x="0" y="5" width="18" height="5" fill="#2b7fc3"/><rect x="0" y="1" width="6" height="4" fill="#2b7fc3"/></svg>3 Beds</span><span><svg width="14" height="14" viewBox="0 0 14 14"><circle cx="7" cy="4" r="3" fill="#2b7fc3"/><rect x="2" y="8" width="10" height="6" rx="2" fill="#2b7fc3"/></svg>8 Guests</span></div>
          <div class="btn">Book Now For £189</div>
        </div>
      </article>
      <article class="card">
        <div class="card-photo" role="img" aria-label="Photo of a lodge lounge" style="background:linear-gradient(150deg,#c2a27b,#634a34)"></div>
        <div class="card-body">
          <div class="card-title">The Marigold</div>
          <div class="card-date">Friday 04 September 2015 (3 nights)</div>
          <div class="card-specs"><span>CARAVAN TYPE</span><span>CARAVAN TYPE</span></div>
          <div class="card-icons"><span><svg width="18" height="12" viewBox="0 0 18 12"><rect x="0" y="5" width="18" height="5" fill="#2b7fc3"/><rect x="0" y="1" width="6" height="4" fill="#2b7fc3"/></svg>3 Beds</span><span><svg width="14" height="14" viewBox="0 0 14 14"><circle cx="7" cy="4" r="3" fill="#2b7fc3"/><rect x="2" y="8" width="10" height="6" rx="2" fill="#2b7fc3"/></svg>8 Guests</span></div>
          <div class="btn">Book Now For £189</div>
        </div>
      </article>
    </div>
  </div>
</section>

<section class="feeds">
  <div class="wrap">
    <div class="feed">
      <div class="feed-head"><svg width="14" height="14" viewBox="0 0 14 14"><rect x="1" y="1" width="12" height="9" fill="#fff"/><path d="M3 10v3l3-3" fill="#fff"/></svg>LATEST REVIEWS</div>
      <div class="review"><h4>HELEN MARSH</h4><div class="stayed">Stayed in The Heathmoor</div><p>Very clean caravan, the staff were friendly and helpful. The kids loved the pool and the beach nearby. We will certainly be booking again next summer.</p></div>
      <div class="review"><h4>CLARE DUNMORE</h4><div class="stayed">Stayed in The Marigold</div><p>Lovely lodge with everything we needed for a week away. Booking was simple and the payment plan made it very easy for our family.</p></div>
      <div class="review"><h4>CLARE DUNMORE</h4><div class="stayed">Stayed in The Marigold</div><p>Great location on the park and close to all the entertainment. Beds were comfy and the kitchen was well stocked. Highly recommended.</p></div>
    </div>
    <div class="feed">
      <div class="feed-head"><svg width="14" height="14" viewBox="0 0 14 14"><rect x="1" y="1" width="12" height="12" fill="none" stroke="#fff" stroke-width="1.6"/><path d="M4 5h6M4 8h6" stroke="#fff" stroke-width="1.4"/></svg>LATEST BLOGS</div>
      <div class="post"><div class="thumb" role="img" aria-label="Photo of a bonfire night event" style="background:linear-gradient(150deg,#a6865e,#4e3b2a)"></div><div><h4>FIREWORKS WEEKEND</h4><p>Join us on the park for a weekend of fireworks, food and fun for all ages.</p><div class="meta">Posted on · 19 August 2015</div></div></div>
      <div class="post"><div class="thumb" role="img" aria-label="Photo of an easter activity" style="background:linear-gradient(150deg,#cfd8c4,#7d8f6c)"></div><div><h4>EASTER WITH FAMILY</h4><p>Plan your spring break early and enjoy our egg hunt and kids club days.</p><div class="meta">Posted on · 19 August 2015</div></div></div>
      <div class="post"><div class="thumb" role="img" aria-label="Photo of an evening show" style="background:linear-gradient(150deg,#8f7a62,#3f3428)"></div><div><h4>FIREWORKS WEEKEND</h4><p>Live music and entertainment in the clubhouse every Saturday night.</p><div class="meta">Posted on · 19 August 2015</div></div></div>
      <div class="post"><div class="thumb" role="img" aria-label="Photo of a lodge veranda" style="background:linear-gradient(150deg,#b8c7a6,#5f7350)"></div><div><h4>FIREWORKS WEEKEND</h4><p>New lodges added to our range for the coming season, book now.</p><div class="meta">Posted on · 19 August 2015</div></div></div>
    </div>
    <div class="feed">
      <div class="feed-head"><svg width="14" height="14" viewBox="0 0 14 14"><circle cx="5" cy="5" r="3" fill="#fff"/><circle cx="10" cy="6" r="2.4" fill="#fff"/><rect x="1" y="9" width="12" height="4" rx="2" fill="#fff"/></svg>SOCIAL FEEDS</div>
      <div class="post"><div class="thumb" role="img" aria-label="Family holiday photo" style="background:linear-gradient(150deg,#9fc0de,#5d8262)"></div><div><h4>MEGAN HOLLIS</h4><p>Had the best week ever at the park, thank you so much.</p><div class="likes"><span>Like</span><span>Comment</span></div></div></div>
      <div class="post"><div class="thumb" role="img" aria-label="Family holiday photo" style="background:linear-gradient(150deg,#d9c09c,#8a6a4a)"></div><div><h4>JANET CORBY</h4><p>Booked again for October half term, cannot wait to return.</p><div class="likes"><span>Like</span><span>Comment</span></div></div></div>
      <div class="post"><div class="thumb" role="img" aria-label="Family holiday photo" style="background:linear-gradient(150deg,#a9cbe2,#6c8f7b)"></div><div><h4>MEGAN HOLLIS</h4><p>Beautiful lodge and lovely staff, highly recommend them.</p><div class="likes"><span>Like</span><span>Comment</span></div></div></div>
      <div class="post"><div class="thumb" role="img" aria-label="Family holiday photo" style="background:linear-gradient(150deg,#e0c9a8,#97795a)"></div><div><h4>MEGAN HOLLIS</h4><p>The kids still talk about the pool, see you next year.</p><div class="likes"><span>Like</span><span>Comment</span></div></div></div>
    </div>
  </div>
</section>

<footer class="site-footer">
  <div class="wrap footer-cols">
    <div class="footer-col"><h5>ABOUT US</h5><ul><li>News</li><li>Caravans &amp; Lodges</li><li>2014 Holidays</li><li>2015 Holidays</li><li>Late Deals</li></ul></div>
    <div class="footer-col"><h5>FERNSIDE CASTLE</h5><ul><li>Local Attractions</li><li>Outside Guest</li><li>Contact Us</li><li>Reviews</li><li>Join Our Social Pages</li></ul></div>
    <div class="footer-col"><h5>FREQUENTLY ASKED QUESTIONS</h5><ul><li>Park Entertainment Passes</li><li>Privacy Policy</li><li>Booking Terms</li></ul></div>
    <div class="footer-col"><h5>NEWS LETTER SUBSCRIPTION</h5><div class="subscribe"></div><div class="btn">Subscribe</div></div>
  </div>
  <div class="footer-bottom">
    <div class="wrap"><span>© Pinebrook Stays. All Rights Reserved</span><span class="top-link">TOP</span></div>
  </div>
</footer>

</body>
</html>
```